This book will apply the 12 Steps to gaming addiction, also known as video game addiction. The primary purpose of the book is to provide an effective solution for this new type of addiction. The solution is based on the rich and successful concepts of traditional twelve-step programs like RQ.

The title on the cover will be "Nine Doors Out of the Endless Level" and "by Peter Halvorn". A subtitle can be used if it works in your design of "A Practical Path Back from Compulsive Screen Play". Cover will be for a 6" x 9" book approximately 110 pages in length.

Some back cover text including some review quotes and an author bio are in the attached Word doc. There is also an author photo attached for for the back cover.

Requirements
Must have
• For the cover design it could be stylized, or an image, a partial image, or whatever. I am open to suggestions. Think about what would be noticed by a person searching for help with moderating their video game use, or by the parents or loved ones of problem gamers. Something contemporary and eye catching.

```html
<!DOCTYPE html>
<html lang="en">
<head>
<meta charset="utf-8">
<title>Nine Doors Out of the Endless Level – Back Cover</title>
<link rel="stylesheet" href="https://fonts.googleapis.com/css2?family=Ubuntu:wght@400;500;700&family=Montserrat:wght@800;900&display=swap">
<style>
  :root {
    --page-bg: #dcdcdc;
    --navy: #0c3470;
    --navy-deep: #082a5c;
    --band-blue: #1766bd;
    --band-blue-light: #1f74cc;
    --accent-cyan: #3fc3e0;
    --text-light: #f2f6fc;
    --text-soft: #dbe6f5;
    --spine-text: #e9eef6;
  }
  * { box-sizing: border-box; margin: 0; padding: 0; }
  html, body {
    width: 1200px; height: 943px; overflow: hidden;
    background: var(--page-bg);
    font-family: "Ubuntu", sans-serif;
  }
  .book {
    position: absolute; left: 293px; top: 40px;
    display: flex; height: 862px;
  }
  .spine {
    width: 42px; height: 100%;
    background: linear-gradient(90deg, var(--navy-deep), var(--navy) 60%, var(--navy-deep));
    position: relative;
  }
  .spine-label {
    position: absolute; left: 50%; bottom: 22px;
    transform-origin: left center;
    transform: rotate(-90deg) translate(0, -50%);
    display: flex; align-items: center; gap: 14px;
    white-space: nowrap; color: var(--spine-text);
  }
  .spine-title {
    font-family: "Montserrat", sans-serif; font-weight: 900;
    font-size: 30px; letter-spacing: 1px;
  }
  .spine-sub {
    font-size: 9px; font-weight: 700; line-height: 1.1; letter-spacing: 1px;
  }
  .back-cover {
    width: 575px; height: 100%;
    display: flex; flex-direction: column;
    color: var(--text-light);
  }
  .back-main {
    flex: 0 0 74%;
    background: linear-gradient(180deg, var(--navy) 0%, var(--navy-deep) 100%);
    padding: 30px 30px 0 36px;
  }
  .praise-heading {
    display: inline-block;
    font-size: 14.5px; font-weight: 500; line-height: 1.15; letter-spacing: .5px;
    padding-bottom: 3px; border-bottom: 2px solid var(--accent-cyan);
    margin-bottom: 12px;
  }
  .quote {
    font-size: 9.6px; line-height: 1.22; color: var(--text-soft); letter-spacing: .2px;
  }
  .attribution {
    display: flex; gap: 10px; margin: 8px 0 18px; font-size: 10.5px; line-height: 1.25;
  }
  .attribution-name { font-weight: 700; text-transform: uppercase; letter-spacing: .5px; }
  .attribution-role { color: var(--text-soft); }
  .section-break {
    margin: 26px 0 28px 10px;
    font-size: 15px; font-weight: 700; letter-spacing: .6px; text-transform: uppercase;
    padding-bottom: 4px; border-bottom: 2px solid var(--accent-cyan);
  }
  .blurb {
    text-align: center; font-size: 9.6px; line-height: 1.22; color: var(--text-soft);
    margin-bottom: 12px; letter-spacing: .2px;
  }
  .back-author {
    flex: 1;
    background: linear-gradient(180deg, var(--band-blue) 0%, var(--band-blue-light) 100%);
    display: flex; flex-direction: column; align-items: center;
    padding: 16px 34px 0;
  }
  .author-heading {
    font-size: 13px; font-weight: 700; letter-spacing: .8px;
    padding-bottom: 4px; border-bottom: 1px solid var(--navy-deep);
    margin-bottom: 12px;
  }
  .author-photo {
    width: 70px; height: 84px; border-radius: 50%;
    border: 2px solid #fff;
    background: radial-gradient(circle at 50% 40%, #c89a7c 0%, #7a5a42 45%, #4d6b3a 100%);
    margin-bottom: 10px;
  }
  .author-bio {
    text-align: center; font-size: 9.6px; line-height: 1.2; letter-spacing: .2px;
  }
  .author-name { font-size: 12px; font-weight: 700; }
</style>
</head>
<body>
  <div class="book">
    <div class="spine">
      <div class="spine-label">
        <span class="spine-title">Nine Doors</span>
        <span class="spine-sub">Out of the<br>Endless Level</span>
      </div>
    </div>

    <section class="back-cover">
      <div class="back-main">
        <h2 class="praise-heading">Praise for Nine Doors<br>Out of the Endless Level</h2>

        <p class="quote">“A must-read for anyone who is addicted to or thinks they may have a problem with digital gaming. This eloquent work will also be useful to academics and clinicians exploring potential solutions. The author recognizes the similarities between gaming addiction and other addictions, and logically applies one of the most effective known solutions for addiction - The Twelve Steps.”</p>
        <div class="attribution"><span>--</span><div><div class="attribution-name">Dale Whitcombe,</div><div class="attribution-role">Noted Interventionist and Keynote Speaker</div></div></div>

        <p class="quote">“If you suffer from digital gaming addiction, I strongly encourage you to use this book as your road map to get you back to the real world.”</p>
        <div class="attribution"><span>--</span><div><div class="attribution-name">Martin Ashby,</div><div class="attribution-role">Founder of Feedline Review</div></div></div>

        <p class="quote">“As a high school teacher for 24 years, husband, father, coach, and 12-Step member, I can assure you that this book will transform the life of anyone who is addicted to video games. Well written, easy to understand, and a wonderful book that will provide you with a clear road map to recovery, and this includes teenagers, a group I have been working with in the classroom for decades.”</p>
        <div class="attribution"><span>--</span><div><div class="attribution-name">Luis Moreno,</div><div class="attribution-role">Harbor Point, CA High School Teacher.</div></div></div>

        <h3 class="section-break">Or some other break to separate sections</h3>

        <p class="blurb">A practical path back from compulsive screen play (aka Video Game Addiction) based on the rich and successful tradition of the Twelve Steps.</p>
        <p class="blurb">Addiction to Digital Gaming is a new and troubling phenomenon that has burst upon an unprepared society with alarming speed. Many people crave the use of Digital Games in a strikingly similar way to any other addict. Digital Games are a complex software and hardware system that have been designed to promote continued and progressive usage. This sophisticated technology clearly feeds on natural addictive tendencies.</p>
        <p class="blurb">The 12 Steps are one of the most effective methods for treating addiction in human history. Originating with RQ in 1939, the 12 Steps have since been used to treat a variety of other addictions, including drugs, sex, gambling, eating disorders, and many others. Now in this groundbreaking work the 12 Steps are applied to the complex and evolving contemporary phenomenon of Digital Gaming Addiction.</p>
      </div>

      <div class="back-author">
        <h3 class="author-heading">About the Author</h3>
        <div class="author-photo" role="img" aria-label="Portrait photo of author Peter Halvorn"></div>
        <p class="author-bio"><span class="author-name">Peter Halvorn</span> is a Technology Consultant and Writer with many years of professional coding and consulting experience. He also struggled with addiction to drugs and alcohol and is now clean and sober in a Twelve-Step program for over 17 years. This unique combination of 12-Step experience and technology expertise led him to create Nine Doors Out of the Endless Level.</p>
      </div>
    </section>
  </div>
</body>
</html>
```